Business card design for Automotive workshop

We need a business card for a new automotive repair and tyre shop called Keelstone Prime Automotive located in New Zealand. We are a clean, modern and fresh workshop and company.

Front needs to feature logo,
my name:
Marlo Fenwicke (director)

Address:
48 Tarn Lane
Marrowby 3584

Phone: 07 594 2713
Mobile: 027 451 9362
Email: office@keelstoneautomotive.example.nz
Website: keelstoneautomotive.example.nz

Back needs to feature an area to write down appointment details, date and time.

Also feature a list of jobs and work we do such as,
Vehicle Servicing
All Mechanical Repairs
Warrant of Fitness
Tyres & Wheel Alignments
Automotive Diagnostics
Automotive Parts & Supplies

```html
<!DOCTYPE html>
<html lang="en">
<head>
<meta charset="utf-8">
<title>Keelstone Prime Automotive – Business Card</title>
<link rel="stylesheet" href="https://fonts.googleapis.com/css2?family=Open+Sans:wght@400;600;700&family=Arimo:wght@400;700&display=swap">
<style>
  :root {
    --brand-red: #e31e24;
    --ink: #1a1a1a;
    --band-black: #0d0d0d;
    --paper: #ffffff;
    --rule: #dcdcdc;
    --backdrop: #e9e7e4;
    --logo-silver: #d9d9d9;
  }
  * { margin: 0; padding: 0; box-sizing: border-box; }
  html, body { width: 1200px; height: 900px; overflow: hidden; }
  body {
    background: var(--backdrop);
    position: relative;
    font-family: "Open Sans", sans-serif;
    color: var(--ink);
  }
  .card {
    position: absolute;
    background: var(--paper);
    overflow: hidden;
    box-shadow: 2px 3px 6px rgba(0,0,0,0.25);
  }
  /* Front */
  .card-front { left: 330px; top: 90px; width: 555px; height: 343px; }
  .brand-name {
    position: absolute;
    font-family: "Open Sans", sans-serif;
    font-weight: 700;
    text-transform: uppercase;
    white-space: nowrap;
  }
  .card-front .brand-name {
    right: 45px; top: 64px;
    font-size: 21px; letter-spacing: 0.5px;
    color: var(--brand-red);
  }
  .holder { position: absolute; left: 31px; top: 156px; }
  .holder-name {
    font-size: 18px; font-weight: 700; color: var(--brand-red);
    text-transform: uppercase; line-height: 24px;
  }
  .holder-role { font-size: 13.5px; line-height: 16px; }
  .holder-rule {
    position: absolute; left: 235px; top: 172px;
    width: 278px; height: 1px; background: var(--rule);
  }
  .contacts { position: absolute; left: 29px; top: 229px; list-style: none; }
  .contacts li {
    display: flex; align-items: center; gap: 6px;
    font-size: 14.5px; line-height: 20.5px;
  }
  .contacts svg { width: 13px; height: 13px; fill: var(--brand-red); flex: none; }
  .address {
    position: absolute; right: 35px; top: 251px;
    text-align: right; font-size: 14.5px; line-height: 20.5px; font-style: normal;
  }
  .front-band { position: absolute; left: 0; bottom: 0; width: 555px; height: 32px; }
  .website {
    position: absolute; right: 34px; bottom: 8px;
    color: var(--paper); font-size: 13.5px; letter-spacing: 0.5px;
    white-space: nowrap;
  }
  /* Back */
  .card-back { left: 330px; top: 469px; width: 559px; height: 344px; }
  .back-header {
    position: absolute; left: 0; top: 0; width: 100%; height: 101px;
    background: var(--band-black);
    display: flex; align-items: center; justify-content: center;
  }
  .card-back .brand-name {
    position: static;
    font-size: 23px; letter-spacing: 0.5px; color: var(--logo-silver);
  }
  .appointment-title {
    position: absolute; left: 0; width: 100%; top: 137px;
    text-align: center; font-family: "Arimo", sans-serif;
    font-weight: 700; font-size: 23px; color: var(--brand-red);
  }
  .appointment-field {
    position: absolute; top: 206px;
    display: flex; align-items: center; gap: 6px;
    font-family: "Arimo", sans-serif; font-size: 18px;
  }
  .appointment-field .write-line { height: 1px; background: var(--rule); }
  .field-date { left: 70px; }
  .field-date .write-line { width: 148px; }
  .field-time { left: 288px; }
  .field-time .write-line { width: 148px; }
  .services {
    position: absolute; left: 0; bottom: 0; width: 100%; height: 71px;
    background: var(--brand-red); color: var(--paper);
    display: flex; flex-direction: column; justify-content: center; align-items: center;
    font-size: 14.5px; line-height: 23px; list-style: none;
  }
  .services .row { display: flex; gap: 6px; align-items: center; white-space: nowrap; }
  .services .dot { width: 5px; height: 5px; background: var(--paper); display: inline-block; }
</style>
</head>
<body>

<section class="card card-front" aria-label="Card front">
  <div class="brand-name">Keelstone Prime Automotive</div>

  <div class="holder">
    <p class="holder-name">Marlo Fenwicke</p>
    <p class="holder-role">Director</p>
  </div>
  <div class="holder-rule"></div>

  <ul class="contacts">
    <li>
      <svg viewBox="0 0 16 16" aria-hidden="true"><path d="M2 5c0-2 3-3 6-3s6 1 6 3v1h-3V5H5v1H2z"/><path d="M4 7h8l2 6H2z"/></svg>
      07 594 2713
    </li>
    <li>
      <svg viewBox="0 0 16 16" aria-hidden="true"><path d="M4.5 1h7a1 1 0 0 1 1 1v12a1 1 0 0 1-1 1h-7a1 1 0 0 1-1-1V2a1 1 0 0 1 1-1zm.5 2v9h6V3z"/></svg>
      027 451 9362
    </li>
    <li>
      <svg viewBox="0 0 16 16" aria-hidden="true"><path d="M1 3h14L8 9z"/><path d="M1 4.5l7 6 7-6V13H1z"/></svg>
      office@keelstoneautomotive.example.nz
    </li>
  </ul>

  <address class="address">48 Tarn Lane<br>Marrowby 3584</address>

  <svg class="front-band" viewBox="0 0 555 32" aria-hidden="true">
    <polygon points="0,22 258,22 274,0 555,0 555,32 0,32" fill="#0d0d0d"/>
    <polygon points="0,7 270,7 264,15 0,15" fill="#e31e24"/>
  </svg>
  <span class="website">keelstoneautomotive.example.nz</span>
</section>

<section class="card card-back" aria-label="Card back">
  <header class="back-header">
    <div class="brand-name">Keelstone Prime Automotive</div>
  </header>

  <h2 class="appointment-title">NEXT APPOINTMENT</h2>
  <div class="appointment-field field-date"><span>DATE</span><span class="write-line"></span></div>
  <div class="appointment-field field-time"><span>TIME</span><span class="write-line"></span></div>

  <div class="services">
    <div class="row">Vehicle Servicing <span class="dot"></span> All Mechanical Repairs <span class="dot"></span> Automotive Parts &amp; Supplies</div>
    <div class="row">Tyres &amp; Wheel Alignments <span class="dot"></span> Automotive Diagnostics <span class="dot"></span> Warrant of Fitness</div>
  </div>
</section>

</body>
</html>
```